This book will apply the 12 Steps to gaming addiction, also known as video game addiction. The primary purpose of the book is to provide an effective solution for this new type of addiction. The solution is based on the rich and successful concepts of traditional twelve-step programs like RQ.

The title on the cover will be "Nine Doors Out of the Endless Level" and "by Peter Halvorn". A subtitle can be used if it works in your design of "A Practical Path Back from Compulsive Screen Play". Cover will be for a 6" x 9" book approximately 110 pages in length.

Some back cover text including some review quotes and an author bio are in the attached Word doc. There is also an author photo attached for for the back cover.

Requirements
Must have
• For the cover design it could be stylized, or an image, a partial image, or whatever. I am open to suggestions. Think about what would be noticed by a person searching for help with moderating their video game use, or by the parents or loved ones of problem gamers. Something contemporary and eye catching.

```html
<!DOCTYPE html>
<html lang="en">
<head>
<meta charset="UTF-8">
<title>Nine Doors Out of the Endless Level — Book Cover</title>
<link rel="stylesheet" href="https://fonts.googleapis.com/css2?family=Orbitron:wght@500;700;800&family=Poppins:wght@400;600;700&display=swap">
<style>
  :root {
    --page-bg: #e9e6e2;
    --cover-black: #07080c;
    --ink-white: #ffffff;
    --ink-soft: #d9dbe0;
    --rule: rgba(255,255,255,0.75);
    --tone-blue: #1b2d5c;
    --tone-violet: #3a1a44;
    --tone-red: #7a0f1a;
    --tone-deep-red: #2e0509;
  }
  * { margin: 0; padding: 0; box-sizing: border-box; }
  html, body {
    width: 1200px; height: 1000px; overflow: hidden;
    background: var(--page-bg);
  }
  .canvas {
    position: relative; width: 1200px; height: 1000px;
    display: flex; align-items: center; justify-content: center;
  }
  .book-cover {
    position: relative; width: 640px; height: 940px;
    background: var(--cover-black);
    overflow: hidden;
    box-shadow: 0 10px 30px rgba(0,0,0,0.25);
  }
  .cover-art {
    position: absolute; left: 0; right: 0; top: 300px; bottom: 0;
    background: linear-gradient(180deg,
      var(--cover-black) 0%,
      var(--tone-blue) 30%,
      var(--tone-violet) 52%,
      var(--tone-red) 78%,
      var(--tone-deep-red) 100%);
  }
  .title-block {
    position: absolute; left: 0; right: 0; top: 50px;
    text-align: center; color: var(--ink-white);
    font-family: 'Orbitron', sans-serif;
  }
  .title-ruled {
    display: flex; align-items: center; justify-content: center;
    gap: 14px; margin: 0 auto; width: 490px;
    font-weight: 700; letter-spacing: 2px;
  }
  .title-ruled::before, .title-ruled::after {
    content: ""; flex: 1; height: 1px; background: var(--rule);
  }
  .title-small { font-size: 28px; line-height: 36px; }
  .title-large { font-size: 70px; line-height: 84px; font-weight: 800; letter-spacing: 0; }
  .title-medium { font-size: 44px; line-height: 56px; font-weight: 700; letter-spacing: 1px; }
  .title-glow { position: relative; display: block; margin-top: 4px; }
  .title-glow::before {
    content: ""; position: absolute; left: 0; right: 0; top: 50%; height: 28px;
    transform: translateY(-50%);
    background: linear-gradient(90deg, transparent, rgba(170,190,230,0.22) 20%, rgba(210,220,245,0.32) 50%, rgba(170,190,230,0.22) 80%, transparent);
  }
  .title-glow span { position: relative; }
  .title-last { font-size: 62px; line-height: 72px; font-weight: 700; letter-spacing: 2px; margin-top: 4px; }
  .endorsement {
    position: absolute; left: 77px; top: 568px; width: 180px;
    font-family: 'Poppins', sans-serif; color: var(--ink-white);
  }
  .endorsement-quote { font-size: 15px; line-height: 21px; font-weight: 600; }
  .endorsement-name { margin-top: 12px; font-size: 14px; font-weight: 700; letter-spacing: 0.3px; }
  .endorsement-role { font-size: 13.5px; line-height: 19px; font-weight: 400; color: var(--ink-soft); }
  .author-name {
    position: absolute; left: 0; right: 0; bottom: 42px; text-align: center;
    font-family: 'Orbitron', sans-serif; font-weight: 700;
    font-size: 46px; letter-spacing: 3px; color: var(--ink-white);
  }
</style>
</head>
<body>
  <main class="canvas">
    <article class="book-cover">
      <div class="cover-art" role="img" aria-label="Cover photograph: a gamer wearing a headset, lit by red and blue screen glow with streams of code and a bright lens flare"></div>

      <header class="title-block">
        <div class="title-ruled title-small">NINE</div>
        <div class="title-large">DOORS OUT</div>
        <div class="title-ruled title-small">OF THE</div>
        <div class="title-medium title-glow"><span>ENDLESS</span></div>
        <div class="title-last">LEVEL</div>
      </header>

      <aside class="endorsement">
        <p class="endorsement-quote">“A must-read for anyone who is addicted to or thinks they may have a problem with digital gaming…”</p>
        <p class="endorsement-name">DANA WHITCOMBE</p>
        <p class="endorsement-role">Noted Interventionist<br>and Keynote Speaker</p>
      </aside>

      <p class="author-name">PETER HALVORN</p>
    </article>
  </main>
</body>
</html>
```